Packaging Design for A Dessert Shop

This is for a Desserts shop . The products are mini Sweets and Desserts .

I have attached a packaging design that we really love . We would like to adjust it based on our logo .

We love the colors variation in boxes and Abstract .

We would like more than one size for variation demonstration , to see how a group of boxes will look together .

Required :4 Boxes and 1or 2 Bag demonstration in a group photo like the one attached . You can play with the shape like rectangle box , Square box , Large and medium size (or also make the same sizes as the inspirational photo attached).

Please do not worry about the dimensions as it will be a second step . First we want to approve the overall design it self .

We did not attach or talk about the products inside the packaging because What concerns us at the moment the Outer group design for the 4 boxes and bag , as a second step we can amend the size or inner requirements if needed .

colors:ANY COMBINATION OF : Gold and white , or , Gold and black , or ,Gold white and black .
IN ADDITION TO A new color for example : Oilish green / Navy / Velvety Red or any recomendation .

You can also use the exact colors in the inspiration photo itself .

please note : We love the inspiration photo we want it as similar as possible but with our own Touch and logo . Our logo is attached . Using your creativity you can add the logo in the packaging in a way that will not destroy the abstract simplicity effect .

Tips: you can use/exctract Elemnts of the boxes from the logo .
you can Place the logo Tamberlo with out the frame to make it more simple (Option only).

If you have any questions please let us know

This contest will give us the opportunity to know the designer better and may have many jobs together in the near future .

Good Luck

```html
<!DOCTYPE html>
<html lang="en">
<head>
<meta charset="utf-8">
<title>Tamberlo Packaging</title>
<link href="https://fonts.googleapis.com/css2?family=Montserrat:wght@300;500&display=swap" rel="stylesheet">
<style>
  :root{
    --stage:#e4e5e7;
    --paper:#ffffff;
    --ink:#45443f;
    --sage:#8aa06d;
    --terracotta:#d2573a;
    --clay:#cf6a55;
    --gold:#e3c25d;
    --apricot:#f5a055;
    --cream:#f6f5f3;
    --line:#3a3936;
  }
  *{margin:0;padding:0;box-sizing:border-box}
  html,body{width:893px;height:1200px;overflow:hidden;background:var(--paper)}
  .canvas{position:relative;width:893px;height:1200px;font-family:"Montserrat",sans-serif;overflow:hidden}
  .stage{position:absolute;left:0;top:0;width:893px;height:1030px;background:var(--stage)}

  .brand-mark{position:absolute;left:35px;top:35px;width:305px;height:170px;display:flex;align-items:center;justify-content:center}
  .brand-name{font-family:"Montserrat",sans-serif;font-weight:500;font-size:40px;color:var(--line);letter-spacing:1px}

  .bag{position:absolute;background:var(--paper);border-top:10px solid var(--ink)}
  .bag-handle{position:absolute;left:0;width:100%;overflow:visible}
  .bag-initial{position:absolute;background:linear-gradient(160deg,#5a5954,#3a3936);opacity:.9;border-radius:40%}
  .bag-label{position:absolute;font-weight:500;font-size:10px;color:var(--gold);letter-spacing:.5px}

  .box{position:absolute;box-shadow:0 6px 14px rgba(0,0,0,.12)}
  .box-art{position:absolute;border-radius:45% 55% 50% 50%}
  .box-label{position:absolute;font-weight:500;font-size:9px;letter-spacing:.4px}

  .box--sage{left:155px;top:450px;width:310px;height:205px;background:var(--sage)}
  .box--clay{left:0;top:575px;width:280px;height:230px;background:var(--clay)}
  .box--cream-apricot{left:320px;top:530px;width:308px;height:210px;background:var(--cream)}
  .box--ink{left:145px;top:675px;width:325px;height:205px;background:var(--ink)}
  .box--cream-ink{left:500px;top:615px;width:340px;height:225px;background:var(--cream)}
  .box--gold{left:315px;top:765px;width:350px;height:255px;background:var(--gold)}

  .palette{position:absolute;left:0;top:1030px;width:893px;height:170px;text-align:center}
  .palette-title{margin-top:28px;font-weight:300;font-size:21px;letter-spacing:1px;color:#555}
  .swatches{display:flex;justify-content:center;gap:17px;margin-top:20px}
  .swatch{width:82px;height:82px;border-radius:50%}
  .swatch--ink{background:var(--ink)}
  .swatch--sage{background:var(--sage)}
  .swatch--terracotta{background:var(--terracotta)}
  .swatch--gold{background:var(--gold)}
  .swatch--apricot{background:var(--apricot)}
  .swatch--white{background:var(--paper);border:1px solid #333}
</style>
</head>
<body>
<main class="canvas">
  <section class="stage">
    <div class="brand-mark"><span class="brand-name">Tamberlo</span></div>

    <div class="bag" style="left:305px;top:195px;width:240px;height:330px">
      <svg class="bag-handle" style="top:-105px" width="240" height="100" viewBox="0 0 240 100"><path d="M60 100 C60 10 180 10 180 100" fill="none" stroke="#f2f2f2" stroke-width="4"/></svg>
      <div class="bag-initial" role="img" aria-label="Large script initial L with a sweeping stroke" style="left:70px;top:90px;width:100px;height:110px"></div>
      <svg style="position:absolute;left:0;top:145px" width="240" height="20"><path d="M0 10 C80 4 160 16 240 8" fill="none" stroke="#3a3936" stroke-width="3"/></svg>
      <span class="bag-label" style="left:70px;top:218px">Tamberlo</span>
    </div>

    <div class="bag" style="left:548px;top:185px;width:317px;height:445px">
      <svg class="bag-handle" style="top:-100px" width="317" height="95" viewBox="0 0 317 95"><path d="M90 95 C90 5 230 5 230 95" fill="none" stroke="#f2f2f2" stroke-width="4"/></svg>
      <div class="bag-initial" role="img" aria-label="Large script initial letter" style="left:40px;top:145px;width:150px;height:110px"></div>
      <span class="bag-label" style="left:75px;top:300px">Tamberlo</span>
    </div>

    <div class="box box--sage">
      <div class="box-art" role="img" aria-label="Abstract gold leaf and seed illustration" style="left:55px;top:40px;width:200px;height:85px;background:var(--gold)"></div>
      <span class="box-label" style="right:20px;bottom:55px;color:var(--gold)">Tamberlo</span>
    </div>
    <div class="box box--cream-apricot">
      <div class="box-art" role="img" aria-label="Abstract orange cacao pod illustration" style="left:95px;top:30px;width:100px;height:150px;background:var(--apricot)"></div>
      <span class="box-label" style="right:50px;top:30px;color:var(--apricot)">Tamberlo</span>
    </div>
    <div class="box box--clay">
      <div class="box-art" role="img" aria-label="White leafy branch illustration" style="left:10px;top:40px;width:250px;height:70px;background:#f1e3dd;opacity:.8"></div>
      <span class="box-label" style="left:90px;top:140px;color:var(--cream)">Tamberlo</span>
    </div>
    <div class="box box--ink">
      <div class="box-art" role="img" aria-label="Abstract gold cracked shell illustration" style="left:70px;top:45px;width:200px;height:110px;background:linear-gradient(150deg,#d8b653,#a98d3f)"></div>
      <span class="box-label" style="left:85px;top:125px;color:var(--cream)">Tamberlo</span>
    </div>
    <div class="box box--cream-ink">
      <div class="box-art" role="img" aria-label="Black leaf and nut branch illustration" style="left:10px;top:30px;width:270px;height:95px;background:var(--ink)"></div>
      <span class="box-label" style="right:40px;bottom:50px;color:var(--ink)">Tamberlo</span>
    </div>
    <div class="box box--gold">
      <div class="box-art" role="img" aria-label="White scattered leaves and flower illustration" style="left:110px;top:35px;width:180px;height:180px;background:#f5ecd0;opacity:.85"></div>
      <span class="box-label" style="left:30px;top:110px;color:var(--cream)">Tamberlo</span>
    </div>
  </section>

  <section class="palette">
    <h2 class="palette-title">COLOR CHEME</h2>
    <div class="swatches">
      <span class="swatch swatch--ink"></span>
      <span class="swatch swatch--sage"></span>
      <span class="swatch swatch--terracotta"></span>
      <span class="swatch swatch--gold"></span>
      <span class="swatch swatch--apricot"></span>
      <span class="swatch swatch--white"></span>
    </div>
  </section>
</main>
</body>
</html>
```